Landing Page and Logo for Auto-Blogging Platform

I created a platform that allows users to start a blog for their business, hobby, charity, etc. I need a landing page where users can learn about the platform, benefits of consistent blogging, SEO value, plans/pricing, etc. The landing page needs to have multiple call to action buttons encouraging the visitor to register/sign up for a free trial.

In addition to the landing page, I need a page for users to establish the settings for their blog. This page should be a fairly simple form, intended for the user to enter a few details to set up their blog:
1. Name of Blog
2. Up to 10 topics and/or keywords the blog should focus on
3. Theme: Color-scheme and logo upload for blog.

I have attached the specifications of the platform's functionality so you can better understand how it works, plans/pricing, etc.

I also need a logo for the business. The name of the platform is PostNook.

Target Market(s)

Website owners, bloggers, business owners

Industry/Entity Type

Technology, Internet, web design

Coding

Coded - Design and coding required

Number of Pages Required

2 page

Colors
0054AA
0677BA
7BADD7
CADEEF
E8F1F8
0094D4
00A9DD
6FCCEA
C7EBF8
E9F6FB

Requirements
Must have
• Eye-catching design but fairly light on content (keep it simple and brief.)
Nice to have
• Eye-catching yet simple design, clean and easy to understand what we are offering.
Should not have
• Too much “wordy” and confusing content.

```html
<!DOCTYPE html>
<html lang="en">
<head>
<meta charset="utf-8">
<title>PostNook – Auto-Blogging Platform</title>
<link rel="stylesheet" href="https://fonts.googleapis.com/css2?family=Lato:wght@400;700;900&display=swap">
<style>
:root{
  --blue:#0677BA;
  --blue-dark:#0054AA;
  --green:#A9C81E;
  --ink:#333;
  --muted:#555;
  --line:#e4e4e4;
  --footer:#3d3d3d;
}
*{box-sizing:border-box;margin:0;padding:0}
html,body{width:1200px;height:3568px;overflow:hidden}
body{position:relative;font-family:'Lato',sans-serif;color:var(--ink);background:#fff}
.abs{position:absolute}
.btn{position:absolute;display:flex;align-items:center;justify-content:center;background:var(--green);color:#fff;font-weight:700;border-radius:3px;text-decoration:none}
.hl{color:var(--blue);font-weight:700}
.hl-green{color:var(--green);font-weight:700}
.section-title{position:absolute;font-size:44px;font-weight:400;white-space:nowrap}

/* hero */
.hero{position:absolute;left:0;top:0;width:1200px;height:686px;background:linear-gradient(90deg,#fbfbf8 0%,#f3f2ec 45%,#e8e7dd 100%);box-shadow:0 3px 5px rgba(0,0,0,.15)}
.hero-visual{position:absolute;left:617px;top:180px;width:583px;height:506px;background:linear-gradient(160deg,#c9cfc0 0%,#a8a89c 55%,#dcdcd4 100%);border-radius:14px 0 0 0}
.brand{position:absolute;left:111px;top:150px;font-size:50px;font-weight:700;color:#4a4a4a;display:flex;align-items:center;gap:14px}
.brand-dot{width:26px;height:26px;background:var(--green);border-radius:4px}
.nav{position:absolute;top:42px;left:547px;display:flex;gap:0;font-size:15px}
.nav a{color:#222;text-decoration:none;height:37px;display:flex;align-items:center;padding:0 10px}
.nav a.active{background:var(--blue);color:#fff;border-radius:3px;font-weight:700}
.welcome{left:111px;top:262px;font-size:33px;color:#444}
.hero-title{left:108px;top:310px;font-size:94px;font-weight:700;color:var(--blue);line-height:1.1}
.hero-text{left:112px;top:431px;width:440px;font-size:20px;line-height:28px;color:#333}

/* pricing */
.card{position:absolute;background:#fff;border:1px solid #ddd;border-radius:10px}
.card.featured{border-color:#b9d8ee;box-shadow:0 0 16px rgba(6,119,186,.25);z-index:2}
.badge{position:absolute;border-radius:50%;color:#fff;display:flex;flex-direction:column;align-items:center;justify-content:center;z-index:3}
.badge::after{content:"";position:absolute;inset:6px;border:2px dashed #fff;border-radius:50%}
.badge .plan{font-size:14px}
.badge .price{font-size:27px;font-weight:900;line-height:1.15}
.badge .per{font-size:14px}
.badge.blue{background:var(--blue)}
.badge.green{background:var(--green)}
.plan-head{position:absolute;text-align:center;font-size:25px;line-height:32px;color:#333}
.features{position:absolute;list-style:none}
.features li{display:flex;gap:9px;border-bottom:1px solid var(--line);font-size:13px;line-height:18px;color:#444;padding:12px 0 13px}
.features li:last-child{border-bottom:none}
.features li svg{flex:none;margin-top:2px}
.features.big li{font-size:15px;line-height:21px;padding:13px 0 14px}

/* about */
.about-visual{position:absolute;left:111px;top:1587px;width:513px;height:526px;border-radius:50% 40% 50% 50%;background:radial-gradient(circle at 45% 55%,#c6dd55 0%,#a9c81e 55%,#dfe8ee 100%)}
.body-text{position:absolute;font-size:15.5px;line-height:23px;color:#444}

/* methods */
.methods{position:absolute;left:111px;top:2196px;width:978px;height:379px;background:var(--blue);border-radius:14px}
.methods .section-title{color:#fff;left:0;width:978px;text-align:center;top:62px}
.step-num{position:absolute;width:66px;height:66px;border:3px solid #fff;border-radius:50%;color:#fff;font-size:26px;font-weight:700;display:flex;align-items:center;justify-content:center}
.step-text{position:absolute;color:#fff;font-size:15.5px;line-height:23px}
.step-card{position:absolute;left:332px;top:143px;width:308px;height:176px;background:#fff;border-radius:6px}
.step-card .step-num{border-color:var(--green);color:var(--green);width:56px;height:56px;font-size:22px;left:126px;top:16px}
.step-card p{position:absolute;left:22px;top:90px;width:264px;text-align:center;font-size:15px;line-height:19px;color:#444}

/* seo */
.seo-visual{position:absolute;left:561px;top:2660px;width:556px;height:527px;border-radius:46% 46% 20% 40%;background:linear-gradient(150deg,#e9e5df 0%,#b7b3c9 45%,#8a7e76 100%)}

/* footer */
.footer{position:absolute;left:0;top:3270px;width:1200px;height:298px;background:var(--footer);color:#fff;text-align:center}
.footer .brand-name{position:absolute;top:52px;width:100%;font-size:55px;font-weight:700}
.footer-nav{position:absolute;top:137px;width:100%;display:flex;justify-content:center;gap:36px;font-size:15px}
.footer-nav a{color:#fff;text-decoration:none}
.social{position:absolute;top:183px;left:537px;display:flex;gap:17px}
.social span{width:30px;height:30px;border-radius:5px;background:#fff}
.social span:first-child{background:var(--green)}
.copyright{position:absolute;top:271px;width:100%;font-size:12.5px}
</style>
</head>
<body>

<header class="hero">
  <div class="hero-visual" role="img" aria-label="Photo of a laptop on a desk showing a blog page, with soft plant background"></div>
  <div class="brand"><span class="brand-dot"></span>PostNook</div>
  <nav class="nav">
    <a class="active" href="#">Home</a>
    <a href="#" style="margin-left:16px">About Us</a>
    <a href="#" style="margin-left:16px">Pricing</a>
    <a href="#" style="margin-left:16px">Benefits</a>
    <a href="#" style="margin-left:16px">SEO Value</a>
    <a href="#" style="margin-left:16px">Contact Us</a>
  </nav>
  <div class="abs welcome">Welcome to</div>
  <h1 class="abs hero-title">PostNook</h1>
  <p class="abs hero-text">Lorem ipsum dolor sit amet, consectetur adipisc elit, sed do eiusmod tempor incididunt ut labore et dolore magna aliqua.</p>
  <a class="btn" href="#" style="left:112px;top:545px;width:137px;height:38px;font-size:16px">Get Started</a>
</header>

<!-- pricing -->
<h2 class="section-title" style="left:0;width:1200px;text-align:center;top:760px">Our <span class="hl">Pricing</span></h2>

<div class="card" style="left:111px;top:960px;width:320px;height:502px"></div>
<div class="card" style="left:772px;top:960px;width:317px;height:502px"></div>
<div class="card featured" style="left:415px;top:927px;width:373px;height:575px"></div>

<div class="badge blue" style="left:214px;top:891px;width:130px;height:130px"><span class="plan">Base Plan</span><span class="price">$9.99</span><span class="per">/mo.</span></div>
<div class="badge green" style="left:528px;top:851px;width:146px;height:146px"><span class="plan" style="font-size:15px">Ultimate Plan</span><span class="price" style="font-size:30px">$24.99</span><span class="per">/mo.</span></div>
<div class="badge blue" style="left:868px;top:891px;width:130px;height:130px"><span class="plan">Premium Plan</span><span class="price">$14.99</span><span class="per">/mo.</span></div>

<div class="plan-head" style="left:131px;top:1041px;width:280px">1 blog post (up to 2,000 words) every month:</div>
<div class="plan-head" style="left:440px;top:1020px;width:325px;z-index:3;font-size:26px;line-height:32px">1 blog post (up to 3,000 words) per day plus unlimited manual posting:</div>
<div class="plan-head" style="left:792px;top:1041px;width:280px">1 blog post (up to 2,000 words) every week:</div>

<ul class="features" style="left:147px;top:1138px;width:258px">
  <li><svg width="15" height="15" viewBox="0 0 16 16"><circle cx="8" cy="8" r="8" fill="#0677BA"/><path d="M4.5 8.2l2.3 2.3 4.7-4.8" stroke="#fff" stroke-width="1.8" fill="none"/></svg>Excepteur sint occaecat cupidatat non proident, mollit anim id est laborum.</li>
  <li><svg width="15" height="15" viewBox="0 0 16 16"><circle cx="8" cy="8" r="8" fill="#0677BA"/><path d="M4.5 8.2l2.3 2.3 4.7-4.8" stroke="#fff" stroke-width="1.8" fill="none"/></svg>Excepteur sint occaecat cupidatat non proident, mollit anim id est laborum.</li>
  <li><svg width="15" height="15" viewBox="0 0 16 16"><circle cx="8" cy="8" r="8" fill="#0677BA"/><path d="M4.5 8.2l2.3 2.3 4.7-4.8" stroke="#fff" stroke-width="1.8" fill="none"/></svg>Excepteur sint occaecat cupidatat non proident, mollit anim id est laborum.</li>
  <li><svg width="15" height="15" viewBox="0 0 16 16"><circle cx="8" cy="8" r="8" fill="#0677BA"/><path d="M4.5 8.2l2.3 2.3 4.7-4.8" stroke="#fff" stroke-width="1.8" fill="none"/></svg>Excepteur sint occaecat cupidatat</li>
</ul>
<ul class="features big" style="left:453px;top:1139px;width:297px;z-index:3">
  <li><svg width="16" height="16" viewBox="0 0 16 16"><circle cx="8" cy="8" r="8" fill="#0677BA"/><path d="M4.5 8.2l2.3 2.3 4.7-4.8" stroke="#fff" stroke-width="1.8" fill="none"/></svg>Excepteur sint occaecat cupidatat non proident, mollit anim id est laborum.</li>
  <li><svg width="16" height="16" viewBox="0 0 16 16"><circle cx="8" cy="8" r="8" fill="#0677BA"/><path d="M4.5 8.2l2.3 2.3 4.7-4.8" stroke="#fff" stroke-width="1.8" fill="none"/></svg>Excepteur sint occaecat cupidatat non proident, mollit anim id est laborum.</li>
  <li><svg width="16" height="16" viewBox="0 0 16 16"><circle cx="8" cy="8" r="8" fill="#0677BA"/><path d="M4.5 8.2l2.3 2.3 4.7-4.8" stroke="#fff" stroke-width="1.8" fill="none"/></svg>Excepteur sint occaecat cupidatat non proident, mollit anim id est laborum.</li>
  <li><svg width="16" height="16" viewBox="0 0 16 16"><circle cx="8" cy="8" r="8" fill="#0677BA"/><path d="M4.5 8.2l2.3 2.3 4.7-4.8" stroke="#fff" stroke-width="1.8" fill="none"/></svg>Excepteur sint occaecat cupidatat</li>
</ul>
<ul class="features" style="left:808px;top:1138px;width:258px">
  <li><svg width="15" height="15" viewBox="0 0 16 16"><circle cx="8" cy="8" r="8" fill="#0677BA"/><path d="M4.5 8.2l2.3 2.3 4.7-4.8" stroke="#fff" stroke-width="1.8" fill="none"/></svg>Excepteur sint occaecat cupidatat non proident, mollit anim id est laborum.</li>
  <li><svg width="15" height="15" viewBox="0 0 16 16"><circle cx="8" cy="8" r="8" fill="#0677BA"/><path d="M4.5 8.2l2.3 2.3 4.7-4.8" stroke="#fff" stroke-width="1.8" fill="none"/></svg>Excepteur sint occaecat cupidatat non proident, mollit anim id est laborum.</li>
  <li><svg width="15" height="15" viewBox="0 0 16 16"><circle cx="8" cy="8" r="8" fill="#0677BA"/><path d="M4.5 8.2l2.3 2.3 4.7-4.8" stroke="#fff" stroke-width="1.8" fill="none"/></svg>Excepteur sint occaecat cupidatat non proident, mollit anim id est laborum.</li>
  <li><svg width="15" height="15" viewBox="0 0 16 16"><circle cx="8" cy="8" r="8" fill="#0677BA"/><path d="M4.5 8.2l2.3 2.3 4.7-4.8" stroke="#fff" stroke-width="1.8" fill="none"/></svg>Excepteur sint occaecat cupidatat</li>
</ul>

<a class="btn" href="#" style="left:205px;top:1397px;width:133px;height:31px;font-size:13px">Get A Proposal</a>
<a class="btn" href="#" style="left:525px;top:1426px;width:153px;height:37px;font-size:15px;z-index:3">Get A Proposal</a>
<a class="btn" href="#" style="left:866px;top:1397px;width:134px;height:31px;font-size:13px">Get A Proposal</a>

<!-- about -->
<div class="about-visual" role="img" aria-label="Smiling woman with glasses beside floating dashboard screens on a green circle"></div>
<h2 class="section-title" style="left:706px;top:1605px">About The <span class="hl">Platform</span></h2>
<p class="body-text" style="left:702px;top:1683px;width:388px">There needs to be a super-admin panel where platform owner/administrator can see users, their activity, manage user access, etc. Each user will have a dashboard where they control their settings such as account information, billing, view blog posts, view blog post topics, etc. From this dashboard, the user can customize the “look and feel” of their blog including theme, hero banner, header, footer, logo, color scheme, etc.</p>
<p class="body-text" style="left:702px;top:1895px;width:388px">The platform will require a list of blog topics. Based on the topics list, the software will need to automatically send prompts to TextMind in the specified intervals (monthly, weekly, or daily), receive the blog content, and post it to the blog.</p>
<a class="btn" href="#" style="left:702px;top:2044px;width:136px;height:37px;font-size:16px">Read More</a>

<!-- methods -->
<section class="methods">
  <h2 class="section-title">Methods To <span class="hl-green">Create Blog Topics</span></h2>
  <div class="step-num" style="left:28px;top:196px">01</div>
  <p class="step-text" style="left:115px;top:206px;width:190px">The user enters them into a table manually</p>
  <div class="step-card">
    <div class="step-num">02</div>
    <p>AI can create the list of blog topics based on a prompt such as: “Provide a list of 52 blog topics for a handyman business’s blog.</p>
  </div>
  <div class="step-num" style="left:685px;top:196px">03</div>
  <p class="step-text" style="left:773px;top:206px;width:190px">The user uploads a list of blog topics in CSV format.</p>
</section>

<!-- seo -->
<h2 class="section-title" style="left:111px;top:2677px">SEO <span class="hl">Value</span></h2>
<p class="body-text" style="left:111px;top:2757px;width:388px">Lorem ipsum dolor sit amet, consectetur adipiscing elit, sed do eiusmod tempor incididunt ut labore et dolore magna aliqua. Ut enim ad minim veniam, quis nostrud exercitation ullamco laboris nisi ut aliquip ex ea commodo consequat. Duis aute irure dolor in reprehenderit in voluptate velit esse cillum dolore eu fugiat nulla pariatur.</p>
<p class="body-text" style="left:111px;top:2920px;width:388px">Sed ut perspiciatis unde omnis iste natus error sit voluptatem accusantium doloremque laudantium, totam rem aperiam, eaque ipsa quae ab illo inventore veritatis et quasi architecto beatae vitae dicta sunt explicabo. Nemo enim ipsam voluptatem quia voluptas sit aspernatur aut odit aut fugit, sed quia consequuntur magni dolores eos qui ratione voluptatem sequi nesciunt.</p>
<a class="btn" href="#" style="left:111px;top:3122px;width:136px;height:37px;font-size:16px">Read More</a>
<div class="seo-visual" role="img" aria-label="Hands typing on a laptop showing a blog page, with floating analytics dashboard screens"></div>

<!-- footer -->
<footer class="footer">
  <div class="brand-name">PostNook</div>
  <nav class="footer-nav">
    <a href="#">Home</a><a href="#">About Us</a><a href="#">Pricing</a><a href="#">Benefits</a><a href="#">SEO Value</a><a href="#">Contact Us</a>
  </nav>
  <div class="social"><span></span><span></span><span></span></div>
  <p class="copyright">Copyright © 2024 PostNook. All rights reserved.</p>
</footer>

</body>
</html>
```